Varnex Consulting Business card design.

See our website www.varnexconsulting.example which will give you a good idea of what we are about. The font is called 'Play'.

I'd like a standout business card in keeping with the themes and branding on the website

Target Market(s)

professionals. HR directors

Industry/Entity Type

Business

Contact Information for Business Card

Varnex Consulting PO Box 3172 Merrowdale NSW 2291 1300 485 193 Gavin Threlkeld Principal email: career@varnexconsulting.example ABN: 71203948865

Font styles to use
Other font styles liked:
• Play

Requirements
Must have
• Must have same design colours and branding as website.
• On back I'd prefer a list of the things we do which appears below the name at the header on the website

```html
<!DOCTYPE html>
<html lang="en">
<head>
<meta charset="utf-8">
<title>Varnex Consulting – Business Card</title>
<link href="https://fonts.googleapis.com/css2?family=Play:wght@400;700&display=swap" rel="stylesheet">
<style>
  :root {
    --navy: #0c2134;
    --brand-text: #d9e1ea;
    --name-blue: #3a8ed4;
    --tag-blue: #4a79a6;
    --paper: #f1f2f4;
    --ink: #1d1f22;
    --rule: #0a0a0a;
    --icon: #4e6f93;
    --stage: #e4e6e9;
    --photo-top: #2f6fd0;
    --photo-mid: #4f8fe6;
    --photo-low: #1d4fa8;
  }
  * { margin: 0; padding: 0; box-sizing: border-box; }
  html, body { width: 1200px; height: 902px; overflow: hidden; }
  body {
    background: var(--stage);
    font-family: "Play", sans-serif;
    display: flex;
    flex-direction: column;
    align-items: center;
    justify-content: center;
    gap: 40px;
  }
  .card {
    position: relative;
    width: 720px;
    height: 400px;
    overflow: hidden;
    box-shadow: 0 6px 18px rgba(0,0,0,.18);
  }

  /* Back */
  .card-back {
    background: var(--navy);
    display: flex;
    flex-direction: column;
    align-items: center;
    justify-content: center;
  }
  .brand {
    color: var(--brand-text);
    font-weight: 400;
    font-size: 58px;
    letter-spacing: 1px;
    line-height: 1;
    white-space: nowrap;
  }
  .services {
    margin-top: 14px;
    color: var(--tag-blue);
    font-size: 17px;
    letter-spacing: 1px;
    white-space: nowrap;
  }

  /* Front */
  .card-front { background: var(--paper); }
  .card-front svg.shapes { position: absolute; inset: 0; }
  .front-header {
    position: absolute;
    right: 26px;
    top: 28px;
    text-align: right;
  }
  .front-header .brand { font-size: 38px; }
  .front-header .services { font-size: 11.5px; margin-top: 8px; letter-spacing: .6px; }
  .abn {
    position: absolute;
    right: 26px;
    top: 124px;
    color: var(--brand-text);
    font-size: 22px;
    letter-spacing: 1px;
  }
  .person {
    position: absolute;
    right: 26px;
    top: 190px;
    text-align: right;
  }
  .person-name { color: var(--name-blue); font-size: 30px; font-weight: 700; line-height: 1.1; }
  .person-role { color: var(--ink); font-size: 20px; margin-right: 26px; }
  .contacts {
    position: absolute;
    right: 26px;
    top: 270px;
    list-style: none;
    text-align: right;
  }
  .contacts li {
    color: var(--ink);
    font-size: 17px;
    line-height: 27px;
    display: flex;
    align-items: center;
    justify-content: flex-end;
    gap: 10px;
    white-space: nowrap;
  }
  .contacts svg { width: 16px; height: 16px; flex: none; }
</style>
</head>
<body>

  <section class="card card-back" aria-label="Card back">
    <div class="brand">Varnex Consulting</div>
    <p class="services">Executive Search | Careers | Coaching | Leadership | Transition</p>
  </section>

  <section class="card card-front" aria-label="Card front">
    <svg class="shapes" width="720" height="400" viewBox="0 0 720 400">
      <defs>
        <linearGradient id="snowSky" x1="0" y1="0" x2="0" y2="1">
          <stop offset="0" stop-color="var(--photo-top)"/>
          <stop offset=".55" stop-color="var(--photo-mid)"/>
          <stop offset="1" stop-color="var(--photo-low)"/>
        </linearGradient>
      </defs>
      <polygon points="180,0 720,0 720,172 342,172" fill="var(--navy)"/>
      <polygon role="img" aria-label="Photo of a snowboarder mid-jump against a blue sky above a snowy peak"
               points="0,0 180,0 342,172 342,400 0,400" fill="url(#snowSky)"/>
      <polyline points="180,0 342,172 342,400" fill="none" stroke="var(--rule)" stroke-width="5"/>
    </svg>

    <div class="front-header">
      <div class="brand">Varnex Consulting</div>
      <p class="services">Executive Search | Careers | Coaching | Leadership | Transition</p>
    </div>
    <p class="abn">ABN: 71203948865</p>

    <div class="person">
      <p class="person-name">Gavin Threlkeld</p>
      <p class="person-role">Principal</p>
    </div>

    <ul class="contacts">
      <li>1300 485 193
        <svg viewBox="0 0 16 16" aria-hidden="true"><rect width="16" height="16" rx="2" fill="var(--icon)"/><path d="M5 4h2l1 2.5-1.3 1a6 6 0 0 0 2.8 2.8l1-1.3L13 10v2a1 1 0 0 1-1 1A8 8 0 0 1 4 5a1 1 0 0 1 1-1z" fill="#fff"/></svg>
      </li>
      <li>career@varnexconsulting.example
        <svg viewBox="0 0 16 16" aria-hidden="true"><rect width="16" height="16" rx="2" fill="var(--icon)"/><rect x="3" y="5" width="10" height="7" fill="none" stroke="#fff" stroke-width="1.2"/><path d="M3 5l5 4 5-4" fill="none" stroke="#fff" stroke-width="1.2"/></svg>
      </li>
      <li>PO Box 3172 Merrowdale NSW 2291
        <svg viewBox="0 0 16 16" aria-hidden="true"><rect width="16" height="16" rx="2" fill="var(--icon)"/><path d="M8 3a3.2 3.2 0 0 0-3.2 3.2C4.8 9 8 13 8 13s3.2-4 3.2-6.8A3.2 3.2 0 0 0 8 3z" fill="#fff"/><circle cx="8" cy="6.2" r="1.2" fill="var(--icon)"/></svg>
      </li>
    </ul>
  </section>

</body>
</html>
```